MBRDC redesign and update stationary bc envelopes.

Stationary, Envelopes, Brochures, Business Card. Need to add second surgeon and two other offices. I need everything to match. I am a oral & maxillofacial surgeon.
Additional surgeon and three office addresses.
Jae Min Park, DMD, MD, INC

3718 Silver Meadow Parkway
El Dorado Hills, CA 95762

642 Lorin Way, Suite 101
Folsom, CA. 95630

2317 Vale Street, Suite 105
Auburn, CA. 95603
Updates

Logo design uploaded. Zapfino Extra/Adobe Garamond/Palatino are fonts used before. Not sure what is on exisiting stationary.

Target Market(s)

Referral dentist and sometimes patients. I am a oral & Maxillofacial surgeon.

Industry/Entity Type

Dental Clinic

Font styles to use
Serif
Script

Requirements
Must have
• Color of existing stationary. Update is possible.
Nice to have
• Conservative/modern
Should not have
• Playful

```html
<!DOCTYPE html>
<html lang="en">
<head>
<meta charset="utf-8">
<title>MBRDC Stationery</title>
<link href="https://fonts.googleapis.com/css2?family=EB+Garamond:wght@400&family=Arimo:wght@400&family=Open+Sans:wght@400;600&display=swap" rel="stylesheet">
<style>
:root{
  --bg:#e4e4e4;
  --paper:#ffffff;
  --green:#6b8e23;
  --ink:#1e1e1e;
  --body:#555555;
  --band:#f6f0c8;
  --band-soft:rgba(246,240,200,0);
  --brown:#6b4f40;
  --cream:#f3ead8;
  --pin:#e8d77a;
}
*{margin:0;padding:0;box-sizing:border-box}
html,body{width:1200px;height:769px;overflow:hidden;background:var(--bg)}
.canvas{position:relative;width:1200px;height:769px}
.sheet{position:absolute;background:var(--paper);box-shadow:0 1px 4px rgba(0,0,0,.25);overflow:hidden}
.abs{position:absolute}
.sans{font-family:Arimo,Arial,sans-serif}
.body-sans{font-family:"Open Sans",Arial,sans-serif}
.brand{display:flex;align-items:center;gap:5px;font-family:"EB Garamond",Georgia,serif;color:var(--green);white-space:nowrap}
.brand-dot{border-radius:50%;background:var(--band);border:1px solid #d9cf8f}
.names{color:var(--green);font-family:"EB Garamond",Georgia,serif;line-height:1.25}
.art-band{position:absolute;left:0;right:0;bottom:0;background:linear-gradient(to bottom,var(--band-soft),var(--band))}
.icon{display:inline-block;vertical-align:-1px;margin-right:3px}
/* letterhead */
.letterhead{left:87px;top:100px;width:437px;height:560px}
.lh-head{left:257px;top:14px;border-left:1px solid #999;padding-left:10px;font-size:6.3px;color:var(--ink);line-height:1.35}
.lh-head .names{font-size:8.2px}
.letter{left:41px;font-size:7px;color:var(--body)}
.letter p{margin-bottom:12px;line-height:12.6px;width:356px}
.lh-foot{left:50px;width:337px;display:flex;font-family:Arimo,Arial,sans-serif;font-size:7.5px;color:var(--ink);text-align:center;line-height:1.25}
.lh-foot div{flex:1}
.lh-foot div+div{border-left:1px solid #999}
/* envelope */
.envelope{left:597px;top:171px;width:508px;height:229px}
.env-head{left:101px;top:16px;font-size:6.3px;color:var(--ink);line-height:1.4}
.env-head .names{font-size:8.2px}
.addr-line{margin-top:3px}
.web{font-family:"EB Garamond",Georgia,serif;color:var(--green);letter-spacing:2px}
.label{left:815px;top:125px;font-family:Arimo,Arial,sans-serif;font-size:18px;color:#8a8a8a}
/* cards */
.card-front{left:607px;top:487px;width:234px;height:139px}
.card-back{left:862px;top:487px;width:234px;height:139px;background:var(--brown)}
.cf-text{left:11px;top:12px;font-size:5.6px;color:var(--ink);line-height:1.45}
.cf-text .names{font-size:8px}
.services{left:12px;top:72px;list-style:none;font-family:"Open Sans",Arial,sans-serif;font-size:5.6px;color:var(--cream);line-height:8.6px}
.services li::before{content:"";display:inline-block;width:3px;height:3px;border-radius:50%;background:var(--pin);margin-right:3px;vertical-align:1px}
.offices{right:11px;top:73px;text-align:right;font-family:"Open Sans",Arial,sans-serif;font-size:5.6px;color:var(--cream);line-height:8.2px}
.offices div{margin-bottom:5px}
</style>
</head>
<body>
<div class="canvas">

  <div class="abs label">Envelope</div>

  <!-- Letterhead -->
  <section class="sheet letterhead">
    <div class="art-band" role="img" aria-label="Soft landscape artwork area" style="height:105px"></div>
    <div class="abs brand" style="left:42px;top:38px;font-size:20px"><span class="brand-dot" style="width:14px;height:14px"></span>MBRDC</div>
    <div class="abs lh-head sans">
      <div class="names">Daniel R. Hartwell, DDS, INC<br>Jae Min Park, DMD, MD, INC</div>
      <div style="margin-top:2px">Diplomates of the American Board of<br>Oral &amp; Maxillofacial Surgery<br>Dental Implants and Oral Surgery</div>
      <div style="margin-top:3px">
        <svg class="icon" width="6" height="6" viewBox="0 0 10 10"><path d="M2 1l2 2-1 1.5c.6 1.3 1.5 2.2 2.5 2.5L7 6l2 2-1.5 1.5C4.5 9 1 5.5.5 2.5z" fill="var(--green)"/></svg>916.555.0142
        <svg class="icon" style="margin-left:3px" width="6" height="6" viewBox="0 0 10 10"><rect x="2" y="0" width="6" height="3" fill="var(--green)"/><rect x="0" y="4" width="10" height="6" fill="var(--green)"/></svg>916.555.0187<br>
        <svg class="icon" width="6" height="5" viewBox="0 0 10 8"><rect width="10" height="8" fill="var(--green)"/><path d="M0 0l5 4 5-4" stroke="#fff" fill="none"/></svg>drhartwell@meadowridgeoralsurgery.com<br>
        <svg class="icon" width="6" height="6" viewBox="0 0 10 10"><circle cx="5" cy="5" r="4.5" fill="none" stroke="var(--green)"/><path d="M.5 5h9M5 .5c-2 3-2 6 0 9M5 .5c2 3 2 6 0 9" stroke="var(--green)" fill="none" stroke-width=".8"/></svg>www.meadowridgeoralsurgery.com
      </div>
    </div>
    <div class="abs letter body-sans" style="top:102px">Issuing Date: May 5, 2018</div>
    <div class="abs letter body-sans" style="top:119px;line-height:8.5px">Name Of Employee Mr. XYZABC<br>Address of Employee<br>Address Line 2 etc..</div>
    <div class="abs letter body-sans" style="top:167px">Dear Mr.XYZABC</div>
    <div class="abs letter body-sans" style="top:190px">
      <p>Lorem Ipsum has been the industry's standard dummy text ever since the 1500s, when an unknown printer took a galley of type and scrambled it to make a type specimen book. It has survived not only five centuries, but also the leap into electronic typesetting, remaining essentially unchanged. It was popularised in the 1960s with the release of Letraset sheets containing Lorem Ipsum passages, and more recently with desktop publishing software like Aldus PageMaker including versions of Lorem Ipsum.</p>
      <p>Lorem Ipsum is simply dummy text of the printing and typesetting industry. Lorem Ipsum has been the industry's standard dummy text ever since the 1500s, when an unknown printer took a galley of type and scrambled it to make a type specimen book.</p>
      <p>It has survived not only five centuries, but also the leap into electronic typesetting, remaining essentially unchanged. It was popularised in the 1960s with the release of Letraset sheets containing Lorem IpsumIpsum passages.</p>
    </div>
    <div class="abs letter body-sans" style="top:381px">Yours Sincerely</div>
    <div class="abs" role="img" aria-label="Handwritten signature of Marcus Ellery" style="left:41px;top:397px;width:100px;height:14px;background:linear-gradient(90deg,#eee,#f7f7f7)"></div>
    <div class="abs body-sans" style="left:41px;top:416px;font-size:8.5px;font-weight:600;color:#333">Marcus Ellery</div>
    <div class="abs letter body-sans" style="top:431px">Managing Director</div>
    <svg class="abs" style="left:52px;top:510px" width="336" height="14" viewBox="0 0 336 14">
      <line x1="0" y1="10" x2="160" y2="10" stroke="#777" stroke-width=".6"/>
      <line x1="176" y1="10" x2="336" y2="10" stroke="#777" stroke-width=".6"/>
      <path d="M168 13c-3-4-4.5-6-4.5-8a4.5 4.5 0 019 0c0 2-1.5 4-4.5 8z" fill="var(--green)"/><circle cx="168" cy="5" r="1.6" fill="#fff"/>
    </svg>
    <div class="abs lh-foot" style="top:530px">
      <div>3718 Silver Meadow Parkway<br>El Dorado Hills, CA 95762</div>
      <div>642 Lorin Way, Suite 101<br>Folsom, CA. 95630</div>
      <div>2317 Vale Street, Suite 105<br>Auburn, CA. 95603</div>
    </div>
  </section>

  <!-- Envelope -->
  <section class="sheet envelope">
    <div class="art-band" role="img" aria-label="Soft landscape artwork area" style="height:100px"></div>
    <div class="abs brand" style="left:14px;top:52px;font-size:17px"><span class="brand-dot" style="width:11px;height:11px"></span>MBRDC</div>
    <div class="abs env-head sans">
      <div class="names">Daniel R. Hartwell, DDS, INC<br>Jae Min Park, DMD, MD, INC</div>
      <div style="margin-top:1px">Diplomates of the American Board of Oral &amp; Maxillofacial Surgery<br>Dental Implants and Oral Surgery</div>
      <div style="margin-top:9px">
        <div class="addr-line"><svg class="icon" width="4" height="6" viewBox="0 0 8 12"><path d="M4 12C1 7 0 5.5 0 4a4 4 0 018 0c0 1.5-1 3-4 8z" fill="var(--green)"/></svg>3718 Silver Meadow Parkway, El Dorado Hills, CA 95762</div>
        <div class="addr-line"><svg class="icon" width="4" height="6" viewBox="0 0 8 12"><path d="M4 12C1 7 0 5.5 0 4a4 4 0 018 0c0 1.5-1 3-4 8z" fill="var(--green)"/></svg>642 Lorin Way, Suite 101 , Folsom, CA. 95630</div>
        <div class="addr-line"><svg class="icon" width="4" height="6" viewBox="0 0 8 12"><path d="M4 12C1 7 0 5.5 0 4a4 4 0 018 0c0 1.5-1 3-4 8z" fill="var(--green)"/></svg>2317 Vale Street, Suite 105, Auburn, CA. 95603</div>
      </div>
    </div>
    <div class="abs web" style="left:167px;top:203px;font-size:9.5px">www.meadowridgeoralsurgery.com</div>
  </section>

  <!-- Business card front -->
  <section class="sheet card-front">
    <div class="art-band" role="img" aria-label="Soft landscape artwork area" style="height:60px"></div>
    <div class="abs brand" style="left:140px;top:56px;font-size:15px"><span class="brand-dot" style="width:10px;height:10px"></span>MBRDC</div>
    <div class="abs cf-text sans">
      <div class="names">Daniel R. Hartwell, DDS, INC<br>Jae Min Park, DMD, MD, INC</div>
      <div>Diplomates of the American Board of<br>Oral &amp; Maxillofacial Surgery<br>Dental Implants and Oral Surgery</div>
      <div style="margin-top:10px">
        <svg class="icon" width="5" height="5" viewBox="0 0 10 10"><path d="M2 1l2 2-1 1.5c.6 1.3 1.5 2.2 2.5 2.5L7 6l2 2-1.5 1.5C4.5 9 1 5.5.5 2.5z" fill="var(--green)"/></svg>916.555.0142<br>
        <svg class="icon" width="5" height="5" viewBox="0 0 10 10"><rect x="2" y="0" width="6" height="3" fill="var(--green)"/><rect x="0" y="4" width="10" height="6" fill="var(--green)"/></svg>916.555.0187<br>
        <svg class="icon" width="5" height="4" viewBox="0 0 10 8"><rect width="10" height="8" fill="var(--green)"/><path d="M0 0l5 4 5-4" stroke="#fff" fill="none"/></svg><i>drhartwell@meadowridgeoralsurgery.com</i>
      </div>
    </div>
    <div class="abs web" style="left:11px;top:114px;font-size:6.5px;letter-spacing:1.2px">www.meadowridgeoralsurgery.com</div>
  </section>

  <!-- Business card back -->
  <section class="sheet card-back">
    <div class="abs brand" style="left:16px;top:24px;font-size:20px;color:var(--cream)"><span class="brand-dot" style="width:12px;height:12px;background:var(--pin);border:none"></span>MBRDC</div>
    <ul class="abs services">
      <li>Dentoalveolar Surgery</li>
      <li>Dental Implant Surgery</li>
      <li>Orthognathic Surgery</li>
      <li>Facial Trauma Surgery</li>
      <li>Preprosthetic and Reconstructive Surgery</li>
      <li>TMJ Disorders and Surgery</li>
      <li>Obstructive Sleep Apnea Surgery</li>
    </ul>
    <div class="abs offices">
      <div>3718 Silver Meadow Parkway <svg width="4" height="6" viewBox="0 0 8 12"><path d="M4 12C1 7 0 5.5 0 4a4 4 0 018 0c0 1.5-1 3-4 8z" fill="var(--pin)"/></svg><br>El Dorado Hills, CA 95762&nbsp;&nbsp;</div>
      <div>2317 Vale Street, Suite 105 <svg width="4" height="6" viewBox="0 0 8 12"><path d="M4 12C1 7 0 5.5 0 4a4 4 0 018 0c0 1.5-1 3-4 8z" fill="var(--pin)"/></svg><br>Auburn, CA. 95603&nbsp;&nbsp;</div>
      <div>642 Lorin Way, Suite 101 <svg width="4" height="6" viewBox="0 0 8 12"><path d="M4 12C1 7 0 5.5 0 4a4 4 0 018 0c0 1.5-1 3-4 8z" fill="var(--pin)"/></svg><br>Folsom, CA. 95630&nbsp;&nbsp;</div>
    </div>
  </section>

</div>
</body>
</html>
```